Urgent Cardiac Consult Request

We need a one page (1/2 pg size) order form for Urgent Cardiac Consults so that Emergency depts and walk -in clinics can fill this out and send forms with patient to our office. The page needs to have clear information, easy to read and to fill out. Our logo and address at the top and on the back side a map showing our location. I am sending a version that I have but the doctors want something different in the way of layout.
They want less information on them. At top - options for exam s: Excercise Stress Echo; Echocardiogram; Holter/Loop recorder (3day / 14 day/ other __); Concsult. Pt info in middle . Bottom : Indication s 1) Chest Pain/SOB 2: Palpatations 3) Other_____ Eyecatching, larger logo, etc Thanks

```html
<!DOCTYPE html>
<html lang="en">
<head>
<meta charset="utf-8">
<title>Urgent Cardiac Referral Form</title>
<link href="https://fonts.googleapis.com/css2?family=Bebas+Neue&family=Roboto:ital,wght@0,400;0,500;0,700;1,400&display=swap" rel="stylesheet">
<style>
  :root {
    --blue: #1c4a7b;
    --red: #9a1f25;
    --paper: #f4f4f6;
    --bar: #dedfe4;
    --ink: #2e2e33;
    --rule: #55575e;
    --backdrop: #e8e8ea;
  }
  * { box-sizing: border-box; margin: 0; padding: 0; }
  html, body { width: 1180px; height: 1200px; overflow: hidden; background: var(--backdrop); }
  body { position: relative; font-family: "Roboto", Arial, sans-serif; color: var(--ink); }

  .referral-form {
    position: absolute; left: 182px; top: 26px;
    width: 627px; height: 882px;
    background: var(--paper);
    transform: scale(1.3); transform-origin: 0 0;
    overflow: hidden;
  }
  .header-art { position: absolute; inset: 0; width: 627px; height: 882px; }
  .form-title {
    position: absolute; left: 36px; top: 36px;
    font-family: "Bebas Neue", "Oswald", sans-serif;
    font-size: 31px; letter-spacing: 0.2px; color: #fff; line-height: 1;
  }
  .brand-seal {
    position: absolute; left: 350px; top: 30px; width: 234px; height: 234px;
    border-radius: 50%; background: #fff; border: 5px solid var(--blue);
    display: flex; align-items: center; justify-content: center; flex-direction: column;
  }
  .brand-name {
    font-weight: 500; color: var(--blue); font-size: 24px; line-height: 1.15;
    text-align: center; letter-spacing: 0.5px;
  }
  .brand-dot { width: 38px; height: 38px; border-radius: 50%; background: var(--red); margin-bottom: 12px; }

  .clinic-contact { position: absolute; left: 41px; top: 194px; font-size: 15px; line-height: 19px; }
  .clinic-contact .city { color: var(--red); }

  .section-bar {
    position: absolute; left: 27px; width: 576px; height: 24px; background: var(--bar);
    font-weight: 700; color: var(--blue); font-size: 17px; letter-spacing: 1px;
    padding-left: 16px; line-height: 25px;
  }
  .check { display: inline-block; width: 17px; height: 17px; border: 2px solid var(--blue); border-radius: 3px; margin-right: 10px; vertical-align: -3px; }
  .option { position: absolute; font-size: 15px; white-space: nowrap; }
  .option-note { position: absolute; font-size: 13.5px; font-style: italic; color: #444; }

  .field-row { position: absolute; left: 42px; right: 28px; display: flex; align-items: flex-end; font-size: 15px; white-space: nowrap; }
  .field-line { flex: 1; border-bottom: 1px solid var(--rule); margin: 0 6px 3px 8px; }
  .field-line.fixed { flex: none; }
  .field-row .check { margin-left: 10px; margin-right: 8px; }

  .footer-band {
    position: absolute; left: 0; right: 0; bottom: 0; height: 42px; background: var(--blue);
    color: #fff; font-size: 13px; font-style: italic; text-align: center; line-height: 44px; letter-spacing: 0.1px;
  }
</style>
</head>
<body>
<main class="referral-form">
  <svg class="header-art" viewBox="0 0 627 882" aria-hidden="true">
    <path d="M0 0 H627 V242 C605 220 585 205 565 193 L420 110 C260 98 110 108 0 124 Z" fill="var(--blue)"/>
    <path d="M0 128 C120 110 250 100 360 106 C250 114 120 132 0 160 Z" fill="var(--red)"/>
    <path d="M565 194 C590 208 610 224 627 242" fill="none" stroke="var(--red)" stroke-width="5"/>
  </svg>

  <h1 class="form-title">Urgent Cardic Referral Form</h1>

  <div class="brand-seal">
    <span class="brand-dot"></span>
    <div class="brand-name">LAKESIDE HEART<br>INSTITUTE</div>
  </div>

  <address class="clinic-contact" style="font-style:normal">
    <div><span class="city">LAKESIDE</span> : 555-014-2290</div>
    <div>1180 Maple Avenue, Suite 201, Lakeside</div>
    <div>Monday - Saturday : 8am-5pm</div>
  </address>

  <div class="section-bar" style="top:284px">REQUEST FOR</div>
  <div class="option" style="left:43px;top:324px"><span class="check"></span>Stress Echo</div>
  <div class="option" style="left:240px;top:324px"><span class="check"></span>EKG</div>
  <div class="option" style="left:359px;top:324px"><span class="check"></span>Holter Monitor</div>
  <div class="option-note" style="left:388px;top:343px">(24hr, 48hr, 72hr, 7days, 14days)</div>
  <div class="option" style="left:43px;top:361px"><span class="check"></span>Echocardiogram</div>
  <div class="option" style="left:240px;top:361px"><span class="check"></span>Consult</div>

  <div class="section-bar" style="top:407px">PATIENT INFORMATION</div>
  <div class="field-row" style="top:450px">Full Name:<span class="field-line"></span></div>
  <div class="field-row" style="top:487px">Date of Birth:<span class="field-line"></span>Gender<span class="check"></span>Male<span class="check" style="margin-left:14px"></span>Female</div>
  <div class="field-row" style="top:520px">Health Card#:<span class="field-line"></span></div>
  <div class="field-row" style="top:555px">Phone:<span class="field-line"></span></div>

  <div class="section-bar" style="top:599px">PHYSICIAN INFORMATION</div>
  <div class="field-row" style="top:643px;left:41px">Physician Name:<span class="field-line"></span>Billing #:<span class="field-line fixed" style="width:76px;margin-right:0"></span></div>
  <div class="field-row" style="top:677px;left:41px">Phone:<span class="field-line"></span>Fax:<span class="field-line fixed" style="width:228px;margin-right:0"></span></div>
  <div class="field-row" style="top:713px;left:41px">Ordering Physician Signature:<span class="field-line fixed" style="width:120px;margin-left:14px"></span>Date:<span class="field-line" style="margin-right:0"></span></div>

  <div class="section-bar" style="top:754px">INDICATIONS</div>
  <div class="field-row" style="top:796px;left:44px"><span class="check" style="margin-left:0"></span>Chest Pain/SOB<span class="check" style="margin-left:18px"></span>Palpatations<span class="check" style="margin-left:14px"></span>Other<span class="field-line" style="margin-left:10px;margin-right:0"></span></div>

  <footer class="footer-band">PLEASE PROVIDE A COMPLETE LIST OF MEDICATIONS AT TIME OF TESTING AND/OR CONSULTATION.</footer>
</main>
</body>
</html>
```